I need a business card for my original fine art pieces

I would like a business card design including a logo design for a new business in the art world. I am based in the Hunter Valley NSW Australia. I am a contemporary figurative, encaustic and wildlife artist. I would like to be able to upload my email and mobile number to this as well. This design should be one that I can incorporate into banners and flyers etc. Id like to incorporate one of my own images or partial image into the background or somewhere below. My initials are RJ and I would like these used as a logo type. I would like the use of some colour and it to be bright and catchy. The final design should communicate artwork custom made and commissions available.

Overview: Original Fine Artworks for sale, online, art galleries etc, Custom made to order and by commission.

Target market is world wide audience and corporate world

My figurative work is painted using acrylics in a lot of natural ochre colours that reflect the Australian Outback, on canvas, linen, paper or board: My encaustic work is created in a contemporary abstract style using a blow torch and a made with a medium of 100% pure bees wax, Damar resin, mixed media and coloured pigments, applied to Birch board. My wildlife are created using coloured pencil and mixed media on a variety of paper types or board.

```html
<!DOCTYPE html>
<html lang="en">
<head>
<meta charset="utf-8">
<title>Rhea Jarrow – Business Card</title>
<link rel="stylesheet" href="https://fonts.googleapis.com/css2?family=Cinzel:wght@600&family=Open+Sans:wght@400;600;700&family=Arimo:wght@400&display=swap">
<style>
  :root {
    --ink: #0c0c0c;
    --ink-soft: #1b1b1b;
    --flame: #ff4a00;
    --white: #ffffff;
    --stage: #e8e4df;
  }
  * { box-sizing: border-box; margin: 0; padding: 0; }
  html, body {
    width: 1200px; height: 900px; overflow: hidden;
    background: var(--stage);
  }
  .canvas { position: relative; width: 1200px; height: 900px; }

  .card {
    position: absolute; left: 260px;
    width: 680px; height: 389px;
    overflow: hidden;
    background: radial-gradient(ellipse at 50% 30%, var(--ink-soft), var(--ink) 75%);
    box-shadow: 0 6px 18px rgba(0,0,0,.18);
  }
  .card--front { top: 40px; }
  .card--back  { top: 471px; }

  /* Front */
  .front-band {
    position: absolute; left: 0; right: 0; top: 100px; height: 122px;
    background: var(--flame);
  }
  .front-mark {
    position: absolute; left: 262px; top: 72px; width: 156px; height: 156px;
  }
  .front-name {
    position: absolute; left: 0; right: 0; top: 228px;
    text-align: center;
    font-family: "Cinzel", serif; font-weight: 600;
    font-size: 40px; letter-spacing: 1px; color: var(--flame);
  }
  .front-tagline {
    position: absolute; left: 0; right: 0; top: 280px;
    text-align: center;
    font-family: "Arimo", sans-serif; font-size: 17px;
    letter-spacing: 3.6px; color: var(--white);
  }

  /* Back */
  .back-lower {
    position: absolute; left: 0; right: 0; top: 222px; bottom: 0;
    background: var(--flame);
  }
  .back-mark {
    position: absolute; left: 92px; top: 45px; width: 134px; height: 134px;
  }
  .back-name {
    position: absolute; left: 240px; top: 70px;
    font-family: "Cinzel", serif; font-weight: 600;
    font-size: 36px; letter-spacing: 1px; color: var(--flame);
  }
  .back-tagline {
    position: absolute; left: 243px; top: 116px;
    font-family: "Arimo", sans-serif; font-size: 15.5px;
    letter-spacing: 3.2px; color: var(--white);
  }
  .contact {
    position: absolute; left: 190px; top: 252px;
    display: flex; align-items: center; gap: 14px;
    font-family: "Open Sans", sans-serif; color: var(--white);
  }
  .person { text-align: right; }
  .person__name { font-weight: 700; font-size: 19px; line-height: 1.2; }
  .person__role { font-size: 15px; line-height: 1.3; }
  .divider { width: 1px; height: 44px; background: var(--white); }
  .lines { font-size: 14.5px; line-height: 1.45; }
  .lines div { display: flex; align-items: center; gap: 6px; }
  .lines svg { width: 12px; height: 12px; fill: var(--white); }
  .website {
    position: absolute; left: 0; right: 0; top: 330px;
    text-align: center; padding-left: 130px;
    font-family: "Open Sans", sans-serif; font-size: 15px; color: var(--white);
  }
</style>
</head>
<body>
<main class="canvas">

  <section class="card card--front" aria-label="Card front">
    <div class="front-band"></div>
    <svg class="front-mark" viewBox="0 0 156 156" aria-hidden="true">
      <circle cx="78" cy="78" r="78" fill="#0c0c0c"/>
      <circle cx="78" cy="78" r="58" fill="none" stroke="#ff4a00" stroke-width="4"/>
    </svg>
    <h1 class="front-name">RHEA JARROW</h1>
    <p class="front-tagline">ORIGINAL FINE ARTWORKS</p>
  </section>

  <section class="card card--back" aria-label="Card back">
    <div class="back-lower"></div>
    <svg class="back-mark" viewBox="0 0 134 134" aria-hidden="true">
      <circle cx="67" cy="67" r="63" fill="none" stroke="#ff4a00" stroke-width="4"/>
    </svg>
    <h2 class="back-name">RHEA JARROW</h2>
    <p class="back-tagline">ORIGINAL FINE ARTWORKS</p>

    <div class="contact">
      <div class="person">
        <div class="person__name">Daniel Hartley</div>
        <div class="person__role">Managing Director</div>
      </div>
      <div class="divider"></div>
      <div class="lines">
        <div>
          <svg viewBox="0 0 24 24" aria-hidden="true"><path d="M6.6 10.8a15.1 15.1 0 0 0 6.6 6.6l2.2-2.2a1 1 0 0 1 1-.25 11.4 11.4 0 0 0 3.6.6 1 1 0 0 1 1 1V20a1 1 0 0 1-1 1A17 17 0 0 1 3 4a1 1 0 0 1 1-1h3.5a1 1 0 0 1 1 1c0 1.25.2 2.45.6 3.6a1 1 0 0 1-.25 1z"/></svg>
          <span>(044)987654321</span>
        </div>
        <div>
          <svg viewBox="0 0 24 24" aria-hidden="true"><path d="M2 5h20v14H2z M2 5l10 8 10-8" fill="none" stroke="#fff" stroke-width="2.4"/></svg>
          <span>hello@rheajarrow.art</span>
        </div>
      </div>
    </div>
    <p class="website">www.rheajarrow.art</p>
  </section>

</main>
</body>
</html>
```